RW Holloway LLC Business Card - Civil Engineering & Consulting Firm

We need a Business Card that is elegant, and masculine.  It is our Professional Civil Engineering & Consulting Company located in San Antonio TX (Not s construction or builder firm- no gears & no tool images please). We provide civil engineering services including  commercial site plans, grading and drainage plans, utility plans, hydraulics and hydrology, land planning, utility coordination, and other general civil engineering services related to commercial and residential development.
We have 2 existing Logos. We would like to convey reliability, strength, trustworthiness and attention to detail.  Blues and orange tones as per logo We are OK with the use of a darker blue in the mix.  We have 2 logo versions - Full Company Name Logo to go on the back of card, & Small Icon Logo for the front w/ personal Info.

Target Market(s)
Architects, Real Estate Developers, Other Strctural Engineers, Surveyers, General Contractors
Industry/Entity Type
Professional Civil Engineering
Contact Information for Business Card
Name, Position, Address, Cell & Office #, email, and company website
Font styles to use
Other font styles liked:
- Avian
Requirements
Should not have
- No Tools, No Gears, no Cranes, or Construction Equipment.

```html
<!DOCTYPE html>
<html lang="en">
<head>
<meta charset="utf-8">
<title>RW Holloway LLC – Business Card</title>
<link rel="stylesheet" href="https://fonts.googleapis.com/css2?family=Jost:wght@300;400&family=Arimo:wght@400&display=swap">
<style>
  :root {
    --stage: #0e0e0f;
    --card: #262729;
    --card-edge: #5b8fd0;
    --blue: #5b9bdc;
    --orange: #e8892b;
    --text: #d9dadc;
    --muted: #b9bbbe;
  }
  * { margin: 0; padding: 0; box-sizing: border-box; }
  html, body { width: 1200px; height: 820px; overflow: hidden; background: var(--stage); }
  .stage {
    position: relative; width: 1200px; height: 820px;
    display: flex; align-items: center; justify-content: center; gap: 50px;
  }
  .card {
    position: relative; width: 540px; height: 308px;
    background: var(--card);
    border-left: 3px solid var(--card-edge);
    border-bottom: 3px solid var(--card-edge);
    box-shadow: 0 20px 40px rgba(0,0,0,.6);
    font-family: "Arimo", Arial, sans-serif;
    color: var(--text);
  }
  /* Front */
  .brand {
    position: absolute; top: 58px; right: 48px;
    display: flex; align-items: center; gap: 12px;
  }
  .brand-mark { width: 22px; height: 22px; background: var(--orange); }
  .brand-name {
    font-family: "Jost", sans-serif; font-weight: 300;
    color: var(--blue); font-size: 38px; letter-spacing: 4px; line-height: 1;
  }
  .rule { position: absolute; height: 1px; background: var(--blue); }
  .rule-top { left: 150px; right: 40px; top: 142px; }
  .rule-mid { left: 36px; width: 220px; top: 214px; }
  .person { position: absolute; left: 36px; top: 158px; }
  .person-name {
    font-family: "Jost", sans-serif; font-weight: 300;
    font-size: 24px; letter-spacing: .5px; text-transform: uppercase;
  }
  .person-name .first { color: var(--blue); }
  .person-name .last { color: var(--orange); }
  .person-role { font-size: 14px; margin-top: 4px; color: var(--text); }
  .contacts { position: absolute; left: 36px; top: 226px; list-style: none; font-size: 13.5px; }
  .contacts li { display: flex; align-items: center; gap: 8px; height: 22px; }
  .contacts svg { width: 14px; height: 14px; flex: none; }
  .contacts .accent { color: var(--orange); }
  .address {
    position: absolute; right: 40px; top: 160px;
    text-align: right; font-size: 13.5px; line-height: 1.4; color: var(--muted);
  }
  /* Back */
  .back-brand {
    position: absolute; right: 48px; top: 104px;
    display: flex; align-items: center; gap: 14px;
  }
  .back-brand .brand-mark { width: 30px; height: 30px; }
  .back-brand .brand-name { font-size: 52px; letter-spacing: 5px; }
  .back-rule { left: 230px; right: 48px; top: 178px; }
  .tagline {
    position: absolute; right: 48px; top: 200px;
    font-size: 14.5px; color: var(--text); letter-spacing: .3px;
  }
</style>
</head>
<body>
<main class="stage">
  <section class="card card-front" aria-label="Card front">
    <div class="brand">
      <span class="brand-mark"></span>
      <span class="brand-name">HOLLOWAY LLC</span>
    </div>
    <div class="rule rule-top"></div>
    <div class="person">
      <p class="person-name"><span class="first">Daniel</span> <span class="last">Whitcombe</span></p>
      <p class="person-role">Managing Director</p>
    </div>
    <div class="rule rule-mid"></div>
    <ul class="contacts">
      <li>
        <svg viewBox="0 0 16 16" fill="none" stroke="var(--blue)" stroke-width="1.6"><path d="M3 2h3l1 3-2 1.5c1 2 2.5 3.5 4.5 4.5L10 9l3 1v3c0 1-1 1.5-2 1.5C6 14 2 10 1.5 5 1.5 3 2 2 3 2z"/></svg>
        044-555 010 246
      </li>
      <li>
        <svg viewBox="0 0 16 16" fill="none" stroke="var(--blue)" stroke-width="1.6"><rect x="1.5" y="3.5" width="13" height="9"/><path d="M1.5 3.5 8 9l6.5-5.5"/></svg>
        info@hollowaycivil.com
      </li>
      <li>
        <svg viewBox="0 0 16 16" fill="none" stroke="var(--blue)" stroke-width="1.4"><circle cx="8" cy="8" r="6.5"/><ellipse cx="8" cy="8" rx="3" ry="6.5"/><path d="M1.5 8h13M3 4.5h10M3 11.5h10"/></svg>
        <span>www.<span class="accent">hollowaycivil</span>.com</span>
      </li>
    </ul>
    <p class="address">118, Meridian Park Drive<br>78205, United States</p>
  </section>

  <section class="card card-back" aria-label="Card back">
    <div class="back-brand">
      <span class="brand-mark"></span>
      <span class="brand-name">HOLLOWAY LLC</span>
    </div>
    <div class="rule back-rule"></div>
    <p class="tagline">Commercial and Residential Development</p>
  </section>
</main>
</body>
</html>
```